Business card for Sports Apparel business

DOUBLE SIDED DESIGN
We need business cards for a new sports apparel business. We are developing a protective headband for soccer initially.
Torvalle is focused on designing and developing head protection products to reduce the likelihood of concussion when playing sports. Exploring and understanding medical insights, material science research, current and former players experiences and governing bodies guidelines has allowed Torvalle to develop the safety, style, form and function requirements of a suitable product to bring to market.
Target Market(s)
Mums buying kits for the sons and daughters. Amateur footballers.
Industry/Entity Type
Sporting Good
Contact Information for Business Card
Martin Ashworth - CEO
Mobile: +44 7431589027
Email: martin@torvalle.co.uk
Tel: 0208 5519372
Helena Pargeter - COO
Mob: +44 7385 640117
Email: helena@torvalle.co.uk
Tel: 0208 5519372
Duncan Farrow - CCO
Mob: +44 7564 293081
Email: duncan@torvalle.co.uk
Tel: 0208 5519372
Look and feel
Each slider illustrates characteristics of the customer's brand and the style your logo design should communicate.

```html
<!DOCTYPE html>
<html lang="en">
<head>
<meta charset="utf-8">
<title>Torvalle Business Card</title>
<link rel="stylesheet" href="https://fonts.googleapis.com/css2?family=Raleway:wght@500;700&family=Arimo:wght@400&display=swap">
<style>
  :root {
    --brand-blue: #005c93;
    --ink: #222222;
    --slate: #6b6b6b;
    --paper: #ffffff;
    --backdrop: #c9c9c9;
  }
  * { margin: 0; padding: 0; box-sizing: border-box; }
  html, body { width: 1200px; height: 802px; overflow: hidden; }
  body { background: var(--backdrop); position: relative; font-family: "Arimo", Arial, sans-serif; }

  .card {
    position: absolute;
    top: 274px;
    width: 443px;
    height: 264px;
    box-shadow: 2px 3px 6px rgba(0,0,0,0.35);
    overflow: hidden;
  }
  .card--front { left: 136px; background: var(--paper); }
  .card--back { left: 624px; background: var(--brand-blue); display: flex; align-items: center; justify-content: center; }

  .person { position: absolute; left: 35px; top: 32px; }
  .person__name {
    font-family: "Raleway", sans-serif;
    font-weight: 700;
    font-size: 19px;
    color: var(--brand-blue);
    letter-spacing: 0.1px;
    line-height: 1;
  }
  .person__role { font-size: 13.5px; color: var(--ink); margin-top: 3px; line-height: 1; }

  .contacts { position: absolute; left: 35px; top: 87px; list-style: none; }
  .contacts__item {
    display: flex; align-items: center; gap: 8px;
    font-size: 13.5px; color: var(--ink);
    height: 19px;
  }
  .contacts__icon { width: 16px; height: 16px; flex: none; }

  .brand-band { position: absolute; left: 0; top: 192px; width: 100%; height: 43px; }
  .brand-band__tab { position: absolute; left: 0; top: 0; width: 16px; height: 43px; background: var(--slate); }
  .brand-band__name {
    position: absolute; left: 35px; top: 0; width: 193px; height: 43px;
    display: flex; align-items: center; justify-content: center;
    font-family: "Raleway", sans-serif; font-weight: 500;
    font-size: 30px; letter-spacing: 1px; color: var(--brand-blue);
  }
  .brand-band__stripe { position: absolute; left: 251px; top: 0; right: 0; height: 43px; background: var(--brand-blue); }

  .back-brand {
    font-family: "Raleway", sans-serif; font-weight: 500;
    font-size: 42px; letter-spacing: 1.5px; color: var(--paper);
  }
</style>
</head>
<body>
  <section class="card card--front" aria-label="Card front">
    <div class="person">
      <p class="person__name">MARTIN ASHWORTH</p>
      <p class="person__role">CEO</p>
    </div>
    <ul class="contacts">
      <li class="contacts__item">
        <svg class="contacts__icon" viewBox="0 0 16 16" aria-hidden="true">
          <rect x="0.75" y="0.75" width="14.5" height="14.5" rx="2" fill="none" stroke="var(--brand-blue)" stroke-width="1.5"/>
          <path d="M5 3.5 L6.8 5.6 L5.8 6.8 Q7 9.2 9.2 10.2 L10.4 9.2 L12.5 11 L11.4 12.5 Q6.5 12 3.6 4.6 Z" fill="var(--brand-blue)"/>
        </svg>
        <span>0208 5519372</span>
      </li>
      <li class="contacts__item">
        <svg class="contacts__icon" viewBox="0 0 16 16" aria-hidden="true">
          <rect x="0.75" y="0.75" width="14.5" height="14.5" rx="2" fill="none" stroke="var(--brand-blue)" stroke-width="1.5"/>
          <rect x="5" y="3.2" width="6" height="9.6" rx="1" fill="none" stroke="var(--brand-blue)" stroke-width="1.3"/>
          <circle cx="8" cy="11.2" r="0.6" fill="var(--brand-blue)"/>
        </svg>
        <span>+44 7431589027</span>
      </li>
      <li class="contacts__item">
        <svg class="contacts__icon" viewBox="0 0 16 16" aria-hidden="true">
          <rect x="0.75" y="0.75" width="14.5" height="14.5" rx="2" fill="none" stroke="var(--brand-blue)" stroke-width="1.5"/>
          <rect x="3.3" y="5" width="9.4" height="6.5" fill="var(--brand-blue)"/>
          <path d="M3.3 5 L8 8.8 L12.7 5" fill="none" stroke="var(--paper)" stroke-width="1"/>
        </svg>
        <span>martin@torvalle.co.uk</span>
      </li>
    </ul>
    <div class="brand-band">
      <div class="brand-band__tab"></div>
      <div class="brand-band__name">TORVALLE</div>
      <div class="brand-band__stripe"></div>
    </div>
  </section>

  <section class="card card--back" aria-label="Card back">
    <p class="back-brand">TORVALLE</p>
  </section>
</body>
</html>
```